Storm Restoration Contractor needs a professional letterhead design

Looking for a professional letterhead design. Not looking for your cheapo MS Word standard ones that are readily available. Dont want it to be cookie cutter look like ones readily available online. We just recently changed our logo and want to freshen up all our documents. Our company handles restoring a property back to a pre-loss condition after a storm damages it. For example, wind, hail, flood, fire losses.

Target Market(s)

Property Owners, Homeowners, Property Owners, Commercial Property Owners, Property Management Companies

Industry/Entity Type

Construction Company

Requirements
Must have
• Professional, Use 1 of 2 logo options
• Storm Restoration, Roofing, Siding, Windows

```html
<!DOCTYPE html>
<html lang="en">
<head>
<meta charset="utf-8">
<title>Northgate Exteriors Letterhead</title>
<link rel="stylesheet" href="https://fonts.googleapis.com/css2?family=Open+Sans:wght@400;700&display=swap">
<style>
  :root {
    --brand-blue: #1b75bc;
    --brand-gray: #6d6e71;
    --ink: #333333;
    --paper: #ffffff;
    --backdrop: #e6e7e9;
  }
  * { margin: 0; padding: 0; box-sizing: border-box; }
  html, body {
    width: 1200px; height: 1200px; overflow: hidden;
    background: var(--backdrop);
    font-family: "Open Sans", sans-serif;
  }
  .letterhead {
    position: absolute; left: 152px; top: 20px;
    width: 896px; height: 1160px;
    background: var(--paper);
  }
  .brand {
    position: absolute; left: 58px; top: 45px;
    display: flex; align-items: center; gap: 16px;
  }
  .brand-mark {
    width: 88px; height: 88px; border-radius: 50%;
    background: var(--brand-blue);
  }
  .brand-name {
    color: var(--brand-blue); font-weight: 700;
    font-size: 34px; line-height: 1.05; letter-spacing: 1px;
    text-transform: uppercase;
  }
  .sender-address {
    position: absolute; right: 57px; top: 53px;
    text-align: right; font-style: normal;
    font-size: 15px; line-height: 17.5px; color: var(--ink);
  }
  .sender-address .company { color: var(--brand-blue); }
  .contact-bar {
    position: absolute; left: 0; right: 0; top: 1116px;
    display: flex; justify-content: center; gap: 14px;
    font-size: 15px; color: var(--ink);
  }
  .contact-item { display: flex; align-items: center; gap: 6px; }
  .contact-item svg { width: 13px; height: 13px; fill: var(--brand-blue); }
  .footer-band {
    position: absolute; left: 0; right: 0; bottom: 0; height: 13px;
    display: flex;
  }
  .footer-band .blue { flex: 1; background: var(--brand-blue); }
  .footer-band .gray { flex: 1; background: var(--brand-gray); }
</style>
</head>
<body>
  <main class="letterhead">
    <header class="brand">
      <div class="brand-mark"></div>
      <div class="brand-name">Northgate<br>Exteriors</div>
    </header>

    <address class="sender-address">
      <span class="company">Northgate Exteriors</span><br>
      482 Alder Park Road<br>
      Suite 310<br>
      Fairmont, VA 22310
    </address>

    <footer class="contact-bar">
      <span class="contact-item">
        <svg viewBox="0 0 16 16"><path d="M11 1l3 3-2 2c-1 2 -3 4-5 5l-2 2-3-3 2-2 2 1c1-1 2-2 3-3l-1-2z"/></svg>
        +1 555 014 2290
      </span>
      <span class="contact-item">
        <svg viewBox="0 0 16 16"><path d="M4 1h8v4H4zM1 6h14v6h-3v3H4v-3H1zM5 10v4h6v-4z"/></svg>
        +1 555 014 2291
      </span>
      <span class="contact-item">
        <svg viewBox="0 0 16 16"><path d="M1 3h14v2L8 9 1 5zM1 7l7 4 7-4v6H1z"/></svg>
        info@northgateext.com
      </span>
      <span class="contact-item">
        <svg viewBox="0 0 16 16"><path d="M8 1a7 7 0 1 0 0 14A7 7 0 0 0 8 1zm0 1.5c.8 0 1.8 2 2 4.5H6c.2-2.5 1.2-4.5 2-4.5zM2.6 7h2.2c0-1.6.4-3 .9-4A5.6 5.6 0 0 0 2.6 7zm7.7-4c.5 1 .9 2.4.9 4h2.2a5.6 5.6 0 0 0-3.1-4zM2.6 9a5.6 5.6 0 0 0 3.1 4c-.5-1-.9-2.4-.9-4zm3.4 0c.2 2.5 1.2 4.5 2 4.5s1.8-2 2-4.5zm5.2 0c0 1.6-.4 3-.9 4a5.6 5.6 0 0 0 3.1-4z"/></svg>
        www.northgateext.com
      </span>
    </footer>

    <div class="footer-band"><span class="blue"></span><span class="gray"></span></div>
  </main>
</body>
</html>
```